Vehicle accessory sales website

We need a refreshed design for our vehicle accessory. This website is used to select vehicle year, make, model, trim and then displays products available for the vehicle you selected. The design needs to be responsive over mobile, tablet and desktop.

Current site: https://kelvorautoparts.example/vehicle-search/

We are only looking for an updated UI on the vehcile search function, not the website itself.

I want one full screen that is a Year, Make, Model and Trim Selection, this is a stamdalone page with no header, not a website page.

Then a screen that shows the vehicle selected at the top (Not a vehicle image) and the available product categories.

Then a screen that still shows the products avaiable after selecting the category

Then a product pop up

Then a checkout screen

Target Market(s)

Car dealership customers and salespeople

Industry/Entity Type

Automotive accessories

Number of Pages Required

3 page

Requirements
Must have
• Vehicle selection page, main category page, product page after category has been selected, product pop up and checkout screen

```html
<!DOCTYPE html>
<html lang="en">
<head>
<meta charset="utf-8">
<title>Select Your Vehicle</title>
<link rel="stylesheet" href="https://fonts.googleapis.com/css2?family=Orbitron:wght@900&family=Montserrat:wght@500&display=swap">
<style>
  :root {
    --bg-top: #1c1d1f;
    --bg-mid: #232527;
    --bg-bottom: #2b2d2f;
    --panel: rgba(18, 18, 19, 0.93);
    --field: #000000;
    --text: #ffffff;
  }
  * { box-sizing: border-box; margin: 0; padding: 0; }
  html, body {
    width: 1200px;
    height: 693px;
    overflow: hidden;
    background: var(--bg-top);
  }
  .stage {
    position: relative;
    width: 1200px;
    height: 693px;
    overflow: hidden;
  }
  .backdrop {
    position: absolute;
    inset: 0;
    background:
      radial-gradient(ellipse at 80% 75%, rgba(60, 70, 78, 0.35), transparent 55%),
      linear-gradient(180deg, var(--bg-top) 0%, var(--bg-mid) 55%, var(--bg-bottom) 100%);
  }
  .vehicle-search {
    position: absolute;
    left: 99px;
    top: 121px;
    width: 1003px;
    height: 452px;
    background: var(--panel);
    border-radius: 34px;
  }
  .vehicle-search__title {
    position: absolute;
    top: 56px;
    left: 0;
    width: 100%;
    text-align: center;
    font-family: "Orbitron", sans-serif;
    font-weight: 900;
    font-size: 27px;
    letter-spacing: 1.5px;
    color: var(--text);
    line-height: 1;
  }
  .selector-grid {
    position: absolute;
    left: 51px;
    top: 141px;
    display: grid;
    grid-template-columns: 443px 443px;
    grid-template-rows: 67px 67px;
    column-gap: 15px;
    row-gap: 15px;
  }
  .selector {
    position: relative;
    background: var(--field);
    display: flex;
    align-items: center;
    color: var(--text);
    font-family: "Montserrat", sans-serif;
    font-weight: 500;
    font-size: 15.5px;
    letter-spacing: 0.2px;
  }
  .selector__icon {
    position: absolute;
    left: 28px;
    top: 50%;
    transform: translateY(-50%);
    width: 24px;
    height: 22px;
  }
  .selector__label { position: absolute; left: 83px; }
  .selector__caret {
    position: absolute;
    left: 387px;
    top: 50%;
    transform: translateY(-50%);
    width: 12px;
    height: 7px;
  }
  .view-button {
    position: absolute;
    left: 358px;
    top: 338px;
    width: 286px;
    height: 62px;
    border: 1px solid var(--text);
    border-radius: 31px;
    background: transparent;
    color: var(--text);
    font-family: "Montserrat", sans-serif;
    font-weight: 500;
    font-size: 20.5px;
    letter-spacing: 0.3px;
    display: flex;
    align-items: center;
    justify-content: center;
  }
</style>
</head>
<body>
<div class="stage">
  <div class="backdrop" role="img" aria-label="Dim photograph of an empty highway stretching toward mountains at dusk"></div>

  <section class="vehicle-search">
    <h1 class="vehicle-search__title">SELECT YOUR VEHICLE</h1>

    <div class="selector-grid">
      <div class="selector">
        <svg class="selector__icon" viewBox="0 0 24 22" aria-hidden="true">
          <path fill="#fff" d="M5 4.5 C5.4 3.3 6.2 2.5 7.6 2.5 H16.4 C17.8 2.5 18.6 3.3 19 4.5 L20.3 8.5 H22.5 V10 H21.2 C22 10.7 22.5 11.6 22.5 12.8 V18 H20 V19.5 H17 V18 H7 V19.5 H4 V18 H1.5 V12.8 C1.5 11.6 2 10.7 2.8 10 H1.5 V8.5 H3.7 Z M6.8 5 L5.8 8.5 H18.2 L17.2 5 C17 4.4 16.7 4.2 16.1 4.2 H7.9 C7.3 4.2 7 4.4 6.8 5 Z M5.2 11.8 A1.6 1.6 0 1 0 5.2 15 A1.6 1.6 0 1 0 5.2 11.8 Z M18.8 11.8 A1.6 1.6 0 1 0 18.8 15 A1.6 1.6 0 1 0 18.8 11.8 Z M9 13 V14.8 H15 V13 Z"/>
        </svg>
        <span class="selector__label">SELECT A MAKE</span>
        <svg class="selector__caret" viewBox="0 0 12 7" aria-hidden="true"><path fill="#fff" d="M0 0 H12 L6 7 Z"/></svg>
      </div>

      <div class="selector">
        <svg class="selector__icon" viewBox="0 0 24 22" aria-hidden="true">
          <g fill="none" stroke="#fff" stroke-width="1.6">
            <rect x="1.5" y="5" width="21" height="15" rx="1"/>
            <line x1="1.5" y1="10" x2="22.5" y2="10"/>
            <circle cx="7" cy="3.5" r="2"/>
            <circle cx="17" cy="3.5" r="2"/>
            <rect x="4" y="12.5" width="4" height="2.5"/>
            <rect x="10" y="12.5" width="4" height="2.5"/>
            <rect x="16" y="12.5" width="4" height="2.5"/>
            <rect x="4" y="16.5" width="4" height="2"/>
            <rect x="10" y="16.5" width="4" height="2"/>
          </g>
        </svg>
        <span class="selector__label">SELECT A YEAR</span>
        <svg class="selector__caret" viewBox="0 0 12 7" aria-hidden="true"><path fill="#fff" d="M0 0 H12 L6 7 Z"/></svg>
      </div>

      <div class="selector">
        <svg class="selector__icon" viewBox="0 0 24 22" aria-hidden="true">
          <path fill="#fff" d="M5 4.5 C5.4 3.3 6.2 2.5 7.6 2.5 H16.4 C17.8 2.5 18.6 3.3 19 4.5 L20.3 8.5 H22.5 V10 H21.2 C22 10.7 22.5 11.6 22.5 12.8 V18 H20 V19.5 H17 V18 H7 V19.5 H4 V18 H1.5 V12.8 C1.5 11.6 2 10.7 2.8 10 H1.5 V8.5 H3.7 Z M6.8 5 L5.8 8.5 H18.2 L17.2 5 C17 4.4 16.7 4.2 16.1 4.2 H7.9 C7.3 4.2 7 4.4 6.8 5 Z M5.2 11.8 A1.6 1.6 0 1 0 5.2 15 A1.6 1.6 0 1 0 5.2 11.8 Z M18.8 11.8 A1.6 1.6 0 1 0 18.8 15 A1.6 1.6 0 1 0 18.8 11.8 Z M9 13 V14.8 H15 V13 Z"/>
        </svg>
        <span class="selector__label">SELECT A MODEL</span>
        <svg class="selector__caret" viewBox="0 0 12 7" aria-hidden="true"><path fill="#fff" d="M0 0 H12 L6 7 Z"/></svg>
      </div>

      <div class="selector">
        <svg class="selector__icon" viewBox="0 0 24 22" aria-hidden="true">
          <path fill="#fff" d="M5 4.5 C5.4 3.3 6.2 2.5 7.6 2.5 H16.4 C17.8 2.5 18.6 3.3 19 4.5 L20.3 8.5 H22.5 V10 H21.2 C22 10.7 22.5 11.6 22.5 12.8 V18 H20 V19.5 H17 V18 H7 V19.5 H4 V18 H1.5 V12.8 C1.5 11.6 2 10.7 2.8 10 H1.5 V8.5 H3.7 Z M6.8 5 L5.8 8.5 H18.2 L17.2 5 C17 4.4 16.7 4.2 16.1 4.2 H7.9 C7.3 4.2 7 4.4 6.8 5 Z M5.2 11.8 A1.6 1.6 0 1 0 5.2 15 A1.6 1.6 0 1 0 5.2 11.8 Z M18.8 11.8 A1.6 1.6 0 1 0 18.8 15 A1.6 1.6 0 1 0 18.8 11.8 Z M9 13 V14.8 H15 V13 Z"/>
        </svg>
        <span class="selector__label">SELECT A TRIM</span>
        <svg class="selector__caret" viewBox="0 0 12 7" aria-hidden="true"><path fill="#fff" d="M0 0 H12 L6 7 Z"/></svg>
      </div>
    </div>

    <div class="view-button">VIEW ACCESSORIES</div>
  </section>
</div>
</body>
</html>
```